American cannabis tech company business card design

Pavrel.com is seeking a modern, professional, and brand-aligned business card that represents our company and its core values: Mission, Story, Values, and Impact. As an innovative cannabis company, we want a business card that is not only visually appealing but also serves as a representation of who we are and what we stand for.

Project Scope: Design a double-sided business card that integrates our brand identity and core values. Incorporate our key brand elements, ensuring a sleek and contemporary aesthetic. Visually reflect our core values (Mission, Story, Values, Impact) in a way that is engaging yet professional.

Target Market(s)

Vendors, third parties,

Contact Information for Business Card

Contact details (name, title, email, phone, website, etc.)

Font styles to use
Other font styles liked:
• Caslon, Centra

Colors

Designer to choose colors to be used in the design.

Requirements
Must have
• Pavrel.com logo and branding A creative yet clean way to integrate our core values (Mission, Story, Values, Impact) Modern typography and a well-structured layout
Nice to have
• forest green, grey, white, black
Should not have
• references to marijuana, leafs, plants, or related product

```html
<!DOCTYPE html>
<html lang="en">
<head>
<meta charset="utf-8">
<title>Pavrel Business Card</title>
<link href="https://fonts.googleapis.com/css2?family=Montserrat:wght@400;700;800&display=swap" rel="stylesheet">
<style>
  :root {
    --backdrop: #d4d9d8;
    --card-stock: #ebebe7;
    --forest: #1b3320;
    --ink-grey: #4a4a48;
  }
  html, body {
    margin: 0;
    padding: 0;
    width: 1200px;
    height: 881px;
    overflow: hidden;
    background: var(--backdrop);
  }
  .canvas {
    position: relative;
    width: 1200px;
    height: 881px;
    display: flex;
    align-items: center;
    justify-content: center;
    gap: 60px;
  }
  .card {
    width: 480px;
    height: 274px;
    background: var(--card-stock);
    border-bottom: 5px solid var(--forest);
    box-shadow: 0 10px 24px rgba(0,0,0,0.12);
    position: relative;
    box-sizing: border-box;
    font-family: 'Montserrat', sans-serif;
  }
  .card--contact {
    display: flex;
    align-items: center;
    justify-content: center;
    gap: 22px;
  }
  .identity {
    text-align: right;
  }
  .identity__name {
    margin: 0;
    font-weight: 700;
    font-size: 17px;
    letter-spacing: 0.5px;
    color: var(--forest);
  }
  .identity__title {
    margin: 4px 0 0;
    font-weight: 400;
    font-size: 12px;
    color: var(--ink-grey);
  }
  .divider {
    width: 2px;
    height: 84px;
    background: var(--forest);
  }
  .contact-list {
    list-style: none;
    margin: 0;
    padding: 0;
  }
  .contact-list__item {
    display: flex;
    align-items: center;
    gap: 9px;
    font-size: 13px;
    color: var(--ink-grey);
    line-height: 24px;
  }
  .contact-list__icon {
    width: 11px;
    height: 11px;
    fill: var(--forest);
    flex: none;
  }
  .card--brand {
    display: flex;
    align-items: center;
    justify-content: center;
  }
  .brand-name {
    margin: 0;
    font-weight: 800;
    font-size: 78px;
    letter-spacing: 1px;
    color: var(--forest);
  }
</style>
</head>
<body>
<main class="canvas">
  <section class="card card--contact" aria-label="Business card contact side">
    <div class="identity">
      <p class="identity__name">DANIEL HART</p>
      <p class="identity__title">Managing Director</p>
    </div>
    <div class="divider"></div>
    <ul class="contact-list">
      <li class="contact-list__item">
        <svg class="contact-list__icon" viewBox="0 0 12 12" aria-hidden="true"><path d="M2.5 1 L4.5 1 L5.2 3.4 L4 4.3 C4.6 5.8 6.2 7.4 7.7 8 L8.6 6.8 L11 7.5 L11 9.5 C11 10.3 10.3 11 9.5 11 C5 11 1 7 1 2.5 C1 1.7 1.7 1 2.5 1 Z"/></svg>
        +1 555-210-4830
      </li>
      <li class="contact-list__item">
        <svg class="contact-list__icon" viewBox="0 0 12 12" aria-hidden="true"><path d="M0.5 2.5 H11.5 V9.5 H0.5 Z M0.5 2.5 L6 6.5 L11.5 2.5" stroke="#ebebe7" stroke-width="0.9"/></svg>
        team@pavrel.com
      </li>
      <li class="contact-list__item">
        <svg class="contact-list__icon" viewBox="0 0 12 12" aria-hidden="true"><circle cx="6" cy="6" r="5.5"/><path d="M0.5 6 H11.5 M6 0.5 C3.5 3 3.5 9 6 11.5 M6 0.5 C8.5 3 8.5 9 6 11.5" stroke="#ebebe7" stroke-width="0.8" fill="none"/></svg>
        www.pavrel.com
      </li>
    </ul>
  </section>
  <section class="card card--brand" aria-label="Business card brand side">
    <p class="brand-name">PAVREL</p>
  </section>
</main>
</body>
</html>
```